BRISKEL Need a luxury modern business card designed.

Need a luxury modern business card designed. refer to the uploaded files for the company name and logo in the zip file under source files. i will making my descion on monday. so please send in before then so if we need to edit we will have the time. we have a trade show coming up and im on a deadline for printer.

Target Market(s)

high end clients

Contact Information for Business Card

Company nAme and logo. Tobias Fennick Co-Founder / Project Manager Office # 555-318-7094 Cell # 555-642-1586 BRISKEL.CA Tobias@briskel-example.ca

Font styles to use
Other font styles liked:
• Modern

Requirements
Must have
• Company name and logo, contact info, using the black, gold and white color scheme.

```html
<!DOCTYPE html>
<html lang="en">
<head>
<meta charset="utf-8">
<title>BRISKEL – Business Card</title>
<link href="https://fonts.googleapis.com/css2?family=Poppins:wght@300;400;500&display=swap" rel="stylesheet">
<style>
  :root {
    --backdrop: #2b2b2c;
    --card: #1b1b1c;
    --card-edge: #111112;
    --gold: #b2a068;
    --white: #f4f4f2;
    --grey: #8d8d8d;
    --rule: #9a9a98;
  }
  * { margin: 0; padding: 0; box-sizing: border-box; }
  html, body {
    width: 1200px; height: 1190px; overflow: hidden;
    background: var(--backdrop);
    font-family: "Poppins", sans-serif;
  }
  .sheet { position: relative; width: 1200px; height: 1190px; }
  .card {
    position: absolute; left: 150px; width: 900px; height: 514px;
    background: radial-gradient(ellipse at 40% 30%, #222223 0%, var(--card) 70%);
    border-radius: 26px;
    box-shadow: 0 18px 40px rgba(0,0,0,.55), inset 0 0 0 1px var(--card-edge);
  }
  .card--front { top: 60px; }
  .card--back { top: 620px; }

  /* wordmark block */
  .wordmark { position: absolute; text-align: center; }
  .wordmark__row { display: flex; align-items: center; justify-content: center; gap: 22px; }
  .wordmark__square { width: 22px; height: 22px; background: var(--gold); }
  .wordmark__name {
    color: var(--white); font-weight: 300; letter-spacing: .18em; line-height: 1;
  }
  .wordmark__tagline {
    display: flex; align-items: center; gap: 14px; margin-top: 14px;
    color: var(--rule); font-weight: 400; letter-spacing: .42em; text-transform: uppercase;
  }
  .wordmark__tagline::before, .wordmark__tagline::after {
    content: ""; flex: 1; height: 1px; background: var(--rule);
  }
  .card--front .wordmark { left: 170px; width: 560px; top: 195px; }
  .card--front .wordmark__name { font-size: 78px; }
  .card--front .wordmark__tagline { font-size: 15px; }

  .card--back .wordmark { left: 60px; width: 410px; top: 210px; }
  .card--back .wordmark__name { font-size: 58px; }
  .card--back .wordmark__tagline { font-size: 12px; margin-top: 12px; }
  .card--back .wordmark__square { width: 16px; height: 16px; }

  .divider {
    position: absolute; left: 505px; top: 110px; width: 1.5px; height: 300px;
    background: var(--gold);
  }

  .contact { position: absolute; left: 545px; top: 118px; }
  .contact__name {
    font-size: 32px; font-weight: 400; color: var(--white); letter-spacing: .02em; line-height: 1.1;
  }
  .contact__name .surname { color: var(--gold); }
  .contact__role { font-size: 19px; font-weight: 300; color: var(--grey); margin-top: 4px; }
  .contact__list { list-style: none; margin-top: 34px; }
  .contact__item {
    display: flex; align-items: center; gap: 16px;
    font-size: 21px; font-weight: 400; color: var(--white); line-height: 1; height: 34px;
  }
  .contact__icon { width: 20px; height: 20px; flex: none; }
  .contact__icon--blank { visibility: hidden; }
</style>
</head>
<body>
<main class="sheet">

  <section class="card card--front" aria-label="Card front">
    <div class="wordmark">
      <div class="wordmark__row">
        <span class="wordmark__square" aria-hidden="true"></span>
        <span class="wordmark__name">BRISKEL</span>
      </div>
      <div class="wordmark__tagline">Luxury Landscapes</div>
    </div>
  </section>

  <section class="card card--back" aria-label="Card back">
    <div class="wordmark">
      <div class="wordmark__row">
        <span class="wordmark__square" aria-hidden="true"></span>
        <span class="wordmark__name">BRISKEL</span>
      </div>
      <div class="wordmark__tagline">Luxury Landscapes</div>
    </div>

    <div class="divider" aria-hidden="true"></div>

    <div class="contact">
      <h1 class="contact__name">TOBIAS <span class="surname">FENNICK</span></h1>
      <p class="contact__role">Co-Founder / Project Manager</p>
      <ul class="contact__list">
        <li class="contact__item">
          <svg class="contact__icon" viewBox="0 0 20 20" aria-hidden="true"><path fill="#b2a068" d="M2 7c0-2 2-3 8-3s8 1 8 3v1h-4V6.5H6V8H2zM5 9h10l2 7H3zM10 10.5a2.5 2.5 0 1 0 0 5a2.5 2.5 0 0 0 0-5z"/></svg>
          555-318-7094
        </li>
        <li class="contact__item">
          <svg class="contact__icon" viewBox="0 0 20 20" aria-hidden="true"><rect x="5" y="2" width="10" height="16" rx="2" fill="none" stroke="#b2a068" stroke-width="1.8"/></svg>
          555-642-1586
        </li>
        <li class="contact__item">
          <svg class="contact__icon" viewBox="0 0 20 20" aria-hidden="true"><g fill="none" stroke="#b2a068" stroke-width="1.4"><circle cx="10" cy="10" r="8"/><ellipse cx="10" cy="10" rx="3.5" ry="8"/><path d="M2 10h16M3.5 6h13M3.5 14h13"/></g></svg>
          BRISKEL.CA
        </li>
        <li class="contact__item">
          <svg class="contact__icon" viewBox="0 0 20 20" aria-hidden="true"><rect x="2" y="4" width="16" height="12" fill="#b2a068"/><path d="M2 4l8 7 8-7" fill="none" stroke="#1b1b1c" stroke-width="1.4"/></svg>
          Tobias@briskel-example.ca
        </li>
      </ul>
    </div>
  </section>

</main>
</body>
</html>
```